Web design for new streaming audio service

We need a homepage design for a new streaming audio service. Our company is called Dunmoral, and we’re basically Vexlo for Audiobooks, Stand-Up Comedy, Lectures, Language Learning, etc. Essentially like Plumtrek for everything audio EXCEPT music.
You don’t have to code the homepage (Design Only), but it should include 3 different designs to work with 1) Web; 2) Phones; 3) Tablets.
Below is a link to a mockup of the web version which gives a good idea of what elements we want. This is just a mockup and we want you to improve it.
Once you download the mockup, please refer to the more detailed instructions below:
The following outlines the design project for the Dunmoral homepage. We have provided a rough mockup of the homepage layout that gives you a general idea of what we’re going for. There are a few elements that we are attached to, and many others where you have complete creative freedom to do whatever you think looks good.
The ZIP file includes the following:
* Mockup to see what we have in mind (dunmoral-homepage-mockup.jpg)
* Text used (dunmoral-homepage-text.txt)
* Raw image of actor (dunmoral-actor1.jpg)
* Raw images for samples (dunmoral-sample-[name].jpg)
Although we have only provided a mockup layout for the web version, we also need you to provide a mobile phone and a tablet version of the design also. It’s very possible the tablet version may be substantially similar to the web version, but the mobile phone version will likely be much different.
All of the raw files are included in the attached ZIP file. Please use our photographs and text as provided although cropping, sizing, etc. is flexible per the instructions below.
Display Requirements:
* Web Version - Minimum resolution 1024x768 (72 dpi) but should look good on 1920x1080 (72 dpi) - Page should be designed to scale to look acceptable in all resolutions in between.
* Phone Version - Minimum Zarno 4 - 640x960 (326 dpi) but should look good on Harlow Quasar T5 - 1920x1080 (441 dpi) - Page should be designed to scale to look acceptable in all resolutions and devices in between.
* Tablet Version - Minimum Bristly Ember QX 7” - 1280x800 (216 dpi) but should also look good on a Tavo Breeze - 2048x1536 (264 dpi) - Page should be designed to scale to look acceptable in all resolutions and devices in between.
Above the Fold - We want to make sure the Dunmoral logo, Member Login Link, Large Photo, Headline, Price, Button, and the first row of sample images are all “Above the fold”. As a general guideline, this means 600 pixels high on a 1024x768 72 dpi web screen. This requirement is less important on Phone versions.
Top Logo Bar - We want to retain the blue bar with the Dunmoral logo on the page, although we are open to a different size, shape and positioning if it greatly enhances the design. Please use the standard logo color, although you are welcome to use either the horizontal or vertical orientation of the logo based on your design.
Text color, font and size - Feel free to design the text in anyway you choose as long as the text is readable on the target platforms.
Buttons - Feel free to use any size, shape and colors for the buttons as long as they are obvious and clickable relative to the page. The only exception is the Chatterly button should follow the Chatterly color scheme and logo treatment (the mockup doesn’t seem 100% correct.)
Top Photograph - We want to retain the large photograph across the top of the screen although final shape and dimensions are flexible.
Size and shape of content samples (i.e. Audiobooks, Stand-Up Comedy, etc.) - Feel free to design the content samples in anyway you choose.
Three Sales Points (i.e. Listen on your Zarno…, All you can enjoy…, etc.) - The Three Sales Points are envisioned to each have a corresponding illustration which you should provide and have rights for. The placeholder is represented by a square next to the text. The color size and shape of these elements are flexible and can be designed in any way you choose.
Opt-in form - Feel free to design the opt-in form in anyway you choose as long as the text is readable and the interactivity is obvious on the target platforms.
Text links and copyright notice - Feel free to design the bottom of the page text links and copyright notice in anyway you choose.
Additional colors, graphic design elements, etc. - Feel free to use any additional colors, graphic design elements, etc. to support your design.
people who want to listen to audio through their mobile devices.
Graphic Design

```html
<!DOCTYPE html>
<html lang="en">
<head>
<meta charset="utf-8">
<title>Dunmoral – Unlimited Listening</title>
<link rel="stylesheet" href="https://fonts.googleapis.com/css2?family=Source+Sans+3:wght@400;600;700&display=swap">
<style>
:root{
  --brand-blue:#5aa9d3;
  --headline:#4a5785;
  --orange-top:#fd9a2a;
  --orange-bottom:#f27a0c;
  --panel-grey:#e3e3e3;
  --form-grey:#7b7b7b;
  --ink:#2b2b2b;
  --muted:#8a8a8a;
  --icon-blue:#4fb3e3;
  --social:#4a5a96;
  --white:#ffffff;
}
*{margin:0;padding:0;box-sizing:border-box}
html,body{width:1200px;height:1197px;overflow:hidden;background:var(--white)}
body{font-family:"Source Sans 3",sans-serif;color:var(--ink);position:relative}

.hero{position:absolute;left:0;top:0;width:1200px;height:562px;
  background:
    radial-gradient(ellipse 320px 260px at 800px 250px,#d9a27e 0%,rgba(214,160,120,.7) 45%,rgba(214,160,120,0) 100%),
    radial-gradient(ellipse 520px 200px at 250px 520px,#4f6a8f 0%,rgba(79,106,143,.6) 50%,rgba(79,106,143,0) 100%),
    linear-gradient(90deg,#f7f5f3 0%,#f4efea 30%,#e9d6c6 55%,#c89a7c 72%,#5f6f86 100%);}
.topbar{position:absolute;left:0;top:27px;width:1200px;height:50px;background:var(--brand-blue)}
.brand{position:absolute;left:264px;top:8px;display:flex;align-items:center;gap:8px;color:var(--white);font-size:27px;font-weight:600}
.brand-dot{width:26px;height:26px;border-radius:50%;background:var(--white)}
.member-login{position:absolute;left:843px;top:16px;display:flex;align-items:center;gap:9px;color:var(--white);font-size:10px;font-weight:600}

.hero-copy{position:absolute;left:130px;top:138px;width:430px;text-align:center}
.hero-title{font-size:43px;font-weight:600;line-height:41px;color:var(--headline)}
.hero-price{margin-top:31px;font-size:24px;font-weight:600;color:var(--headline)}
.cta{display:block;margin:17px auto 0;width:276px;height:45px;border-radius:2px;border:1px solid #e56f08;
  background:linear-gradient(var(--orange-top),var(--orange-bottom));color:var(--white);font-family:inherit;font-size:27px;font-weight:600;line-height:42px}
.cta-note{margin-top:12px;font-size:16px;font-weight:600;color:var(--ink)}

.samples{position:absolute;left:0;top:562px;width:1200px;height:404px;background:var(--panel-grey)}
.samples-title{position:absolute;top:21px;width:100%;text-align:center;font-size:22px;font-weight:600;color:var(--ink)}
.sample{position:absolute;display:flex;align-items:center}
.cover{width:74px;height:74px}
.sample-label{font-size:13.5px;font-weight:600;line-height:19px;color:var(--ink)}

.perk{position:absolute;top:880px;display:flex;align-items:center}
.perk-text{font-size:12.5px;font-weight:600;line-height:13px;color:var(--muted)}

.signup{position:absolute;left:0;top:966px;width:1200px;height:164px;background:var(--form-grey);color:var(--white)}
.signup-title{position:absolute;left:264px;top:39px;font-size:16px;font-weight:600}
.signup-copy{position:absolute;left:264px;top:70px;font-size:8px;line-height:12.5px}
.signup-copy p+p{margin-top:12px;font-weight:600}
.email{position:absolute;left:454px;top:42px;width:246px;height:31px;background:var(--white);border:1px solid #ccc;font-family:inherit;font-size:8px;padding-left:13px;color:#666}
.access{position:absolute;left:753px;top:42px;width:184px;height:32px;border:1px solid #e56f08;border-radius:2px;background:linear-gradient(var(--orange-top),var(--orange-bottom));color:var(--white);font-family:inherit;font-size:12px;font-weight:600}
.or{position:absolute;left:753px;top:79px;width:184px;text-align:center;font-size:11px;font-weight:600}
.social{position:absolute;left:753px;top:99px;width:184px;height:32px;border:1px solid #3b4a80;border-radius:2px;background:var(--social);color:var(--white);font-family:inherit;font-size:12px;font-weight:600;display:flex;align-items:center;justify-content:center;gap:8px}
.social-square{width:15px;height:15px;background:var(--white)}

.footer{position:absolute;left:0;top:1130px;width:1200px;height:66px;background:var(--brand-blue);color:var(--white);text-align:center;font-size:8px}
.footer-links{margin-top:18px}
.footer-links span{margin:0 4px}
.copyright{margin-top:11px}
</style>
</head>
<body>

<section class="hero" role="img" aria-label="Photo of a smiling young man wearing headphones and looking at his phone"></section>

<header class="topbar">
  <div class="brand"><span class="brand-dot"></span>Dunmoral</div>
  <div class="member-login">
    <svg width="14" height="11" viewBox="0 0 14 11" aria-hidden="true"><circle cx="5" cy="3" r="2.6" fill="#fff"/><path d="M0 11c0-3 2-4.6 5-4.6s5 1.6 5 4.6z" fill="#fff"/><circle cx="10" cy="3.4" r="2.2" fill="#fff"/><path d="M10.5 6.6c2 .3 3.5 1.6 3.5 4.4h-3c0-2-.3-3.2-.5-4.4z" fill="#fff"/></svg>
    Member Login
  </div>
</header>

<div class="hero-copy">
  <h1 class="hero-title">Unlimited Listening<br>Wherever you are</h1>
  <p class="hero-price">Only $9.99 per month</p>
  <button class="cta">Start Your Free Trial</button>
  <p class="cta-note">* Credit Card Not Required</p>
</div>

<section class="samples">
  <h2 class="samples-title">A sample of what you can listen to on Dunmoral</h2>
</section>

<div class="sample" style="left:262px;top:642px"><div class="cover" role="img" aria-label="Audiobook cover" style="background:linear-gradient(#3a4a55,#1d2a33)"></div><p class="sample-label" style="margin-left:19px">Audio<br>Books</p></div>
<div class="sample" style="left:426px;top:642px"><div class="cover" role="img" aria-label="Stand-up comedy album cover" style="background:linear-gradient(#e9e3d6,#b7a691)"></div><p class="sample-label" style="margin-left:18px">Stand-Up<br>Comedy</p></div>
<div class="sample" style="left:594px;top:642px"><div class="cover" role="img" aria-label="Language course cover" style="background:linear-gradient(#2f93d8,#123c6b)"></div><p class="sample-label" style="margin-left:14px">Language<br>Learning</p></div>
<div class="sample" style="left:768px;top:642px"><div class="cover" role="img" aria-label="Biography cover" style="background:linear-gradient(#c9b69d,#8fc26a)"></div><p class="sample-label" style="margin-left:19px">Biographies &amp;<br>Memoirs</p></div>

<div class="sample" style="left:263px;top:752px"><div class="cover" role="img" aria-label="Guided meditation cover" style="background:linear-gradient(#b14fa8,#5a3c8c)"></div><p class="sample-label" style="margin-left:13px">Guided<br>Meditations</p></div>
<div class="sample" style="left:426px;top:753px"><div class="cover" role="img" aria-label="Business training cover" style="background:linear-gradient(#6b2a1a,#2b1410)"></div><p class="sample-label" style="margin-left:18px">Business<br>Training</p></div>
<div class="sample" style="left:595px;top:753px"><div class="cover" role="img" aria-label="Fitness program cover" style="background:linear-gradient(#3b2a26,#c99a5a)"></div><p class="sample-label" style="margin-left:17px">Fitness<br>Programs</p></div>
<div class="sample" style="left:767px;top:754px"><div class="cover" role="img" aria-label="Celebrity interview cover" style="background:linear-gradient(#2fa7d8,#1a6f9a)"></div><p class="sample-label" style="margin-left:21px">Celebrity<br>Interviews</p></div>

<div class="perk" style="left:259px">
  <svg width="50" height="50" viewBox="0 0 50 50" aria-hidden="true"><path d="M7 28a18 18 0 0 1 36 0" fill="none" stroke="#4fb3e3" stroke-width="4"/><rect x="2" y="24" width="9" height="15" rx="4" fill="#4fb3e3"/><rect x="39" y="24" width="9" height="15" rx="4" fill="#4fb3e3"/><path d="M43 39c0 6-6 8-14 8" fill="none" stroke="#4fb3e3" stroke-width="2.5"/><circle cx="27" cy="47" r="3" fill="#4fb3e3"/></svg>
  <p class="perk-text" style="margin-left:30px">Listen on your<br>Zarno, Tavo or<br>Ferrolite device.</p>
</div>
<div class="perk" style="left:532px">
  <svg width="60" height="52" viewBox="0 0 60 52" aria-hidden="true"><path d="M4 34 26 12h14v14L18 48z" fill="#4fb3e3"/><circle cx="34" cy="18" r="2.5" fill="#e3e3e3"/><path d="M34 18c4-8 10-12 16-12" fill="none" stroke="#4fb3e3" stroke-width="1.5"/></svg>
  <p class="perk-text" style="margin-left:7px">All you can enjoy<br>for one low<br>monthly price.</p>
</div>
<div class="perk" style="left:790px">
  <svg width="44" height="44" viewBox="0 0 44 44" aria-hidden="true"><circle cx="22" cy="22" r="21" fill="#4fb3e3"/><path d="M14 14l16 16M30 14 14 30" stroke="#fff" stroke-width="4" stroke-linecap="round"/></svg>
  <p class="perk-text" style="margin-left:18px">No obligation<br>Cancel any time</p>
</div>

<section class="signup">
  <h3 class="signup-title">Start Your Free Trial</h3>
  <div class="signup-copy">
    <p>You will get instant &amp; unlimited access<br>to all the material on Dunmoral for 14 days.<br>There is no obligation &amp; you can cancel at any time.</p>
    <p>Credit Card Not Required for Free Trial</p>
  </div>
  <input class="email" type="text" placeholder="Your Email Address">
  <button class="access">Get Instant Access</button>
  <p class="or">OR</p>
  <button class="social"><span class="social-square"></span>Sign Up Using Chatterly</button>
</section>

<footer class="footer">
  <p class="footer-links">About<span>|</span>Help<span>|</span>Contact Us<span>|</span>Member Login<span>|</span>Privacy Policy<span>|</span>Terms of Service</p>
  <p class="copyright">©2014 Dunmoral LLC - All Rights Reserved</p>
</footer>

</body>
</html>
```